Business Card Design for a Software Startup

We'd like to have a business card design. We already have a logo. Basically what we need is a clean design with name, address, cellphone and phone numbers, e-mail and web site address (front) and a space on the back with our logo with the company name on the right side and some texts on the bottom.
We are a development and consulting company in Brazil with highly qualified team of professionals in Java, iOS and Android development and consulting.

Target Market(s)

CIO, IT managers of mid to big size companies

Industry/Entity Type

Business

```html
<!DOCTYPE html>
<html lang="en">
<head>
<meta charset="utf-8">
<title>Velora Business Card</title>
<link rel="stylesheet" href="https://fonts.googleapis.com/css2?family=Arimo:wght@400;700&family=Montserrat:wght@800&display=swap">
<style>
  :root {
    --stage: #e9e9ee;
    --navy: #0b4577;
    --navy-deep: #083a68;
    --indigo: #2f3770;
    --sky: #1fa0e0;
    --white: #ffffff;
    --ink: #123f6d;
  }
  * { margin: 0; padding: 0; box-sizing: border-box; }
  html, body {
    width: 1200px;
    height: 987px;
    overflow: hidden;
    background: var(--stage);
  }
  .stage {
    position: relative;
    width: 1200px;
    height: 987px;
  }
  .card {
    position: absolute;
    left: 220px;
    width: 760px;
    height: 434px;
    border-radius: 24px;
    overflow: hidden;
    box-shadow: 0 6px 18px rgba(20, 40, 70, 0.18);
  }
  .card-front { top: 40px; background: var(--white); }
  .card-back {
    top: 513px;
    background: linear-gradient(160deg, #0d5a92 0%, var(--navy) 45%, var(--navy-deep) 100%);
  }
  .front-art { position: absolute; inset: 0; }
  .brand {
    position: absolute;
    display: flex;
    align-items: center;
    gap: 14px;
    font-family: "Montserrat", sans-serif;
    font-weight: 800;
    letter-spacing: 1px;
  }
  .brand-front {
    left: 0;
    right: 0;
    top: 78px;
    justify-content: center;
    color: var(--ink);
    font-size: 44px;
  }
  .brand-mark {
    display: inline-block;
    width: 46px;
    height: 46px;
    border-radius: 8px;
    background: var(--sky);
  }
  .contact {
    position: absolute;
    font-family: "Arimo", sans-serif;
    color: var(--white);
  }
  .contact-person {
    right: 440px;
    top: 292px;
    text-align: right;
  }
  .person-name { font-size: 26px; font-weight: 700; line-height: 30px; }
  .person-title { font-size: 18px; line-height: 24px; }
  .person-address { font-size: 17px; line-height: 22px; }
  .contact-divider {
    position: absolute;
    left: 340px;
    top: 300px;
    width: 1px;
    height: 110px;
    background: rgba(255, 255, 255, 0.55);
  }
  .contact-lines {
    left: 362px;
    top: 300px;
    list-style: none;
    font-size: 19px;
    line-height: 27px;
  }
  .brand-back {
    left: 0;
    right: 0;
    top: 150px;
    justify-content: center;
    color: var(--white);
    font-size: 96px;
    letter-spacing: 3px;
  }
  .back-url {
    position: absolute;
    left: 0;
    right: 0;
    top: 290px;
    text-align: center;
    font-family: "Arimo", sans-serif;
    font-weight: 700;
    font-size: 22px;
    letter-spacing: 8px;
    color: var(--white);
  }
</style>
</head>
<body>
<main class="stage">
  <section class="card card-front" aria-label="Card front">
    <svg class="front-art" width="760" height="434" viewBox="0 0 760 434" aria-hidden="true">
      <defs>
        <linearGradient id="accent-line" x1="0" y1="0" x2="1" y2="0">
          <stop offset="0" stop-color="#1b6fb0"/>
          <stop offset="1" stop-color="#2bb3f0"/>
        </linearGradient>
      </defs>
      <path d="M0,60 C100,230 400,330 760,320 L760,434 L0,434 Z" fill="var(--navy)"/>
      <path d="M0,58 C30,100 40,110 48,112 C20,90 10,70 0,58 Z" fill="var(--indigo)"/>
      <path d="M0,40 L24,40 C60,120 110,190 170,235 C80,180 30,110 0,60 Z" fill="var(--indigo)"/>
      <path d="M30,45 C120,215 380,300 640,318" fill="none" stroke="url(#accent-line)" stroke-width="4"/>
    </svg>

    <div class="brand brand-front"><span class="brand-mark"></span>VELORA</div>

    <div class="contact contact-person">
      <p class="person-name">Your Name</p>
      <p class="person-title">Title</p>
      <p class="person-address">Door No. Street Name</p>
      <p class="person-address">City Name, State, Zip Code</p>
    </div>
    <div class="contact-divider"></div>
    <ul class="contact contact-lines">
      <li>p: 123-456-7890</li>
      <li>c: 123-456-7890</li>
      <li>e: yourname@velora.com</li>
      <li>w: www.velora.com</li>
    </ul>
  </section>

  <section class="card card-back" aria-label="Card back">
    <div class="brand brand-back">VELORA</div>
    <p class="back-url">www.velora.com</p>
  </section>
</main>
</body>
</html>
```